Harbor Crestline (Business Card Design)

Need business cards designed. Something modern, chic, and sleek. Mabye the back of the card should be the navy blue that is in the logo and then just the logo on the back.

Target Market(s)

Those in the hotel, office, and renovation industry

Contact Information for Business Card

1. Logo 2. Dorian Fenwick 3. CEO/Founder 4. Phone: (833) HarbCre / (833) 427-2731 5. Email: dorian@theharborcrestline.com 6. Website: www.theharborcrestline.com

Font styles to use
Other font styles liked:
• Look at the logo font and base the font for everything else off of that.

Colors
0054AA
0677BA
7BADD7
CADEEF
E8F1F8

Requirements
Must have
• Colors that are associated in the logo
Nice to have
• Sleek modern clean and chic design.

```html
<!DOCTYPE html>
<html lang="en">
<head>
<meta charset="utf-8">
<title>Harbor Crestline — Business Card</title>
<link rel="stylesheet" href="https://fonts.googleapis.com/css2?family=Montserrat:wght@400;500;700;800&family=Open+Sans:wght@400;600&display=swap">
<style>
  :root {
    --stage: #222326;
    --navy: #0c1647;
    --navy-deep: #081035;
    --navy-light: #1c2868;
    --gold: #c9a042;
    --white: #ffffff;
    --muted: #dfe3f2;
  }
  * { margin: 0; padding: 0; box-sizing: border-box; }
  html, body { width: 1200px; height: 780px; overflow: hidden; }
  body { background: var(--stage); position: relative; font-family: "Open Sans", Arial, sans-serif; }

  .card {
    position: absolute;
    top: 230px;
    width: 555px;
    height: 318px;
    background: var(--navy);
    border-bottom: 3px solid var(--gold);
    border-left: 2px solid var(--gold);
    overflow: hidden;
  }
  .card--back { left: 30px; }
  .card--front { left: 615px; }

  /* back side */
  .pattern-field {
    position: absolute; inset: 0;
    background: linear-gradient(160deg, var(--navy-light) 0%, var(--navy) 45%, var(--navy-deep) 100%);
  }
  .wordmark {
    position: absolute;
    display: flex; align-items: center; gap: 14px;
    font-family: "Montserrat", Arial, sans-serif;
    font-weight: 700;
    color: var(--white);
    text-transform: uppercase;
    white-space: nowrap;
  }
  .wordmark__square { background: var(--gold); flex: none; }
  .card--back .wordmark {
    left: 50%; top: 50%; transform: translate(-50%, -50%);
    font-size: 34px; letter-spacing: 3px;
  }
  .card--back .wordmark__square { width: 16px; height: 16px; }

  /* front side */
  .accent-tab {
    position: absolute; top: 0; right: 26px;
    width: 14px; height: 62px; background: var(--gold);
  }
  .person {
    position: absolute; top: 16px; right: 52px; text-align: right;
  }
  .person__name {
    font-family: "Montserrat", Arial, sans-serif;
    font-weight: 800; font-size: 27px; color: var(--gold); line-height: 1.1;
  }
  .person__title {
    font-family: "Montserrat", Arial, sans-serif;
    font-weight: 500; font-size: 12px; color: var(--white); letter-spacing: .5px;
  }
  .mark-field {
    position: absolute; top: 92px; right: 36px;
    width: 180px; height: 150px;
    background: linear-gradient(180deg, #3b4682 0%, #1a2462 45%, var(--navy-deep) 100%);
    opacity: .85;
  }
  .card--front .wordmark {
    left: 32px; top: 112px; font-size: 19px; letter-spacing: 2px; gap: 10px;
  }
  .card--front .wordmark__square { width: 11px; height: 11px; }

  .address {
    position: absolute; left: 32px; top: 166px;
    font-size: 12.5px; line-height: 1.45; color: var(--muted);
  }
  .contacts {
    position: absolute; left: 32px; top: 218px;
    list-style: none; font-size: 12.5px; color: var(--muted);
  }
  .contacts li { display: flex; align-items: center; gap: 9px; line-height: 1.65; }
  .contacts svg { width: 13px; height: 13px; flex: none; }
</style>
</head>
<body>

  <section class="card card--back" aria-label="Card back">
    <div class="pattern-field" role="img" aria-label="Repeating small monogram pattern in tonal navy"></div>
    <div class="wordmark"><span class="wordmark__square"></span>Harbor Crestline</div>
  </section>

  <section class="card card--front" aria-label="Card front">
    <div class="accent-tab"></div>
    <div class="person">
      <p class="person__name">Dorian Fenwick</p>
      <p class="person__title">CEO/Founder</p>
    </div>
    <div class="mark-field" role="img" aria-label="Large embossed brand symbol in glossy navy"></div>

    <div class="wordmark"><span class="wordmark__square"></span>Harbor Crestline</div>

    <p class="address">4120 Larkmoor Ave<br>Suite 2200, Easton, MD 21601</p>

    <ul class="contacts">
      <li>
        <svg viewBox="0 0 16 16" aria-hidden="true"><path fill="#c9a042" d="M3.6 1.5l2.2 2.6-1.3 1.6c.9 2 2.4 3.6 4.5 4.6l1.6-1.3 2.7 2.1-1.2 2.4C7 13.2 2.6 8.8 1.3 3l2.3-1.5z"/></svg>
        (833) HarbCre / (833) 427-2731
      </li>
      <li>
        <svg viewBox="0 0 16 16" aria-hidden="true"><g fill="none" stroke="#c9a042" stroke-width="1.4"><circle cx="8" cy="8" r="6.3"/><ellipse cx="8" cy="8" rx="2.8" ry="6.3"/><path d="M1.8 8h12.4"/></g></svg>
        www.theharborcrestline.com
      </li>
      <li>
        <svg viewBox="0 0 16 16" aria-hidden="true"><g fill="none" stroke="#c9a042" stroke-width="1.4"><rect x="1.5" y="3.5" width="13" height="9" rx="1"/><path d="M1.8 4l6.2 5 6.2-5"/></g></svg>
        dorian@theharborcrestline.com
      </li>
    </ul>
  </section>

</body>
</html>
```